Brell Stone Company Business Cards

Front and Back Business Card - logo and text setup - cool design. I need workable photoshop or illustrator files so I can setup each employee card with design that is created
Updates

Hi everyone, thank you for the great entries. Please no more white and blue cards - there are so many already - black and silver only now please. thanks!

Target Market(s)

Construction Industry - Facility Managers

Industry/Entity Type

Construction

Contact Information for Business Card

I really like contemporary simplistic looks - clean neat....not opposed to seeing some black backrounds

Requirements
Must have
• Logo/website address with design on front only - www.brellstone-example.com (logo attached)
• Back:
• Name/Title/Company Address/Phone/email address
Nice to have
• Cool design
Should not have
• Nothing gimmicky like Fire or Water - since we are a Fire Protection company - it has all been done

```html
<!DOCTYPE html>
<html lang="en">
<head>
<meta charset="utf-8">
<title>Brell Stone Company – Business Cards</title>
<link href="https://fonts.googleapis.com/css2?family=Open+Sans:wght@400;700;800&display=swap" rel="stylesheet">
<style>
  :root {
    --page-bg: #262626;
    --card-bg: #0f0f0f;
    --text-main: #f2f2f2;
    --text-soft: #cfcfcf;
    --accent-red: #ff2a1f;
    --rule-grey: #8a8a8a;
  }
  * { margin: 0; padding: 0; box-sizing: border-box; }
  html, body {
    width: 1200px; height: 960px; overflow: hidden;
    background: var(--page-bg);
    font-family: "Open Sans", Arial, sans-serif;
  }
  .sheet {
    width: 1200px; height: 960px;
    display: flex; flex-direction: column; align-items: center; justify-content: center;
    gap: 32px;
  }
  .card {
    position: relative;
    width: 760px; height: 434px;
    background: var(--card-bg);
    border-radius: 4px;
    box-shadow: 0 10px 30px rgba(0,0,0,.45);
    overflow: hidden;
  }
  .wordmark {
    font-weight: 800;
    color: var(--accent-red);
    letter-spacing: -1px;
    line-height: 1;
    white-space: nowrap;
  }

  /* Front */
  .card--front .wordmark {
    position: absolute; left: 0; right: 0; top: 150px;
    text-align: center; font-size: 64px;
  }
  .card--front .front-url {
    position: absolute; left: 0; right: 0; top: 262px;
    text-align: center; font-size: 17px; letter-spacing: 4px;
    color: var(--text-soft);
  }

  /* Back */
  .card--back .wordmark {
    position: absolute; right: 56px; top: 70px; font-size: 46px;
  }
  .holder { position: absolute; left: 62px; top: 112px; }
  .holder__name { font-size: 22px; font-weight: 700; color: var(--text-main); }
  .holder__title { font-size: 19px; color: var(--text-soft); margin-top: 2px; }
  .divider-rule {
    position: absolute; left: 62px; right: 56px; top: 190px; height: 2px;
    background: var(--rule-grey);
  }
  .divider-rule::before {
    content: ""; position: absolute; left: 0; top: -1px;
    width: 120px; height: 4px; background: var(--accent-red);
  }
  .contacts {
    position: absolute; left: 62px; top: 212px;
    list-style: none;
  }
  .contacts li {
    display: flex; align-items: center; gap: 12px;
    font-size: 17px; color: var(--text-main); height: 32px;
  }
  .contacts svg { width: 16px; height: 16px; fill: none; stroke: var(--text-main); stroke-width: 1.6; }
  .address {
    position: absolute; left: 360px; top: 242px;
    padding-left: 18px; border-left: 1px solid var(--rule-grey);
    font-size: 17px; line-height: 28px; color: var(--text-main);
  }
</style>
</head>
<body>
<main class="sheet">
  <section class="card card--front" aria-label="Card front">
    <div class="wordmark">Brell Stone</div>
    <div class="front-url">www.brellstone-example.com</div>
  </section>

  <section class="card card--back" aria-label="Card back">
    <div class="wordmark">Brell Stone</div>
    <div class="holder">
      <div class="holder__name">Dana Morrow</div>
      <div class="holder__title">President</div>
    </div>
    <div class="divider-rule"></div>
    <ul class="contacts">
      <li>
        <svg viewBox="0 0 16 16" aria-hidden="true"><path d="M4 1.5l2.5 3-1.5 1.8a9 9 0 0 0 4.7 4.7l1.8-1.5 3 2.5-1.5 2.2C8 14 2 8 1.8 3z"/></svg>
        (555) 014-2290
      </li>
      <li>
        <svg viewBox="0 0 16 16" aria-hidden="true"><rect x="1.5" y="3.5" width="13" height="9"/><path d="M1.5 3.5l6.5 5 6.5-5"/></svg>
        info@brellstone-example.com
      </li>
      <li>
        <svg viewBox="0 0 16 16" aria-hidden="true"><circle cx="8" cy="8" r="6.5"/><ellipse cx="8" cy="8" rx="2.8" ry="6.5"/><path d="M1.5 8h13"/></svg>
        www.brellstone-example.com
      </li>
    </ul>
    <address class="address" style="font-style:normal">
      48 Harbor Works Road<br>
      Westfield, NY 10990
    </address>
  </section>
</main>
</body>
</html>
```